Luxury WordPress Website for CORALBASINS

I need a professional WordPress website for Coral Basins. The site should be modern, visually appealing, and user-friendly, reflecting the brand’s luxury and premium identity. It must include a homepage, product/service pages, contact form, and be responsive on both desktop and mobile devices. The design should allow for easy updates and integration of future content, while maintaining a polished and professional look.

Target Market(s)

swimmingpool & spa

Industry/Entity Type

Swimmingpool

Coding

Coded - Design and coding required

Font styles to use
Other font styles liked:
• HaboroSoft

Requirements
Must have
• Exclusive appearance
Nice to have
• • A logo that subtly incorporates water or pool elements. • A color palette that reflects luxury, elegance, and relaxation. • Clean and modern typography that is easy to read across all media. • Iconography or design elements that convey premium quality. • A versatile design that can be adapted for social media, merchandise, and promotional materials. • Optional: A tagline that emphasizes luxury and high-end pool experiences.

```html
<!DOCTYPE html>
<html lang="en">
<head>
<meta charset="utf-8">
<title>Coral Basins — The Art of Luxury Pool Design</title>
<link href="https://fonts.googleapis.com/css2?family=Kumbh+Sans:wght@500;600;700;800&family=Lato:wght@400;700&display=swap" rel="stylesheet">
<style>
:root{
  --navy:#0f2a47;
  --navy-deep:#1b3a58;
  --ink:#1a1f2b;
  --text:#4a4f5a;
  --muted:#6b7280;
  --ice:#eef8fc;
  --line:#cfd6de;
  --white:#ffffff;
  --star:#f5a623;
  --cta-grey:#bfc1c4;
}
*{box-sizing:border-box;margin:0;padding:0}
html,body{width:1200px;height:3720px;overflow:hidden}
body{font-family:'Lato',sans-serif;color:var(--text);background:var(--white);position:relative}
.abs{position:absolute}
h1,h2,h3,.display{font-family:'Kumbh Sans',sans-serif;color:var(--ink)}
.eyebrow{font-family:'Lato',sans-serif;font-size:21px;color:var(--ink);letter-spacing:.2px;padding-bottom:6px;border-bottom:2px solid var(--line);display:inline-block}
.btn{display:inline-flex;align-items:center;gap:14px;background:var(--navy);color:var(--white);border-radius:20px;font-size:15px;padding:0 6px 0 14px;height:35px}
.btn .arrow{width:26px;height:26px;border-radius:50%;background:var(--white);display:flex;align-items:center;justify-content:center}
.btn.light{background:var(--white);color:var(--navy)}
.btn.light .arrow{background:var(--navy)}

/* header */
.site-header{top:0;left:0;width:1200px;height:94px;background:var(--white)}
.brand{display:flex;align-items:center;gap:10px}
.brand-dot{width:30px;height:30px;border-radius:50%;background:var(--navy)}
.brand-name{font-family:'Kumbh Sans',sans-serif;font-weight:700;font-size:22px;color:var(--navy);line-height:1}
.brand-tag{font-size:12px;color:var(--navy);margin-top:3px}
.nav a{position:absolute;top:36px;font-size:17px;color:var(--text);text-decoration:none}
.nav a.active{color:var(--navy);font-weight:700;text-decoration:underline}

/* hero */
.hero{top:94px;left:0;width:1200px;height:494px;background:linear-gradient(180deg,#6f7a70 0%,#5c7683 35%,#3f9cc0 60%,#67b8d2 80%,#9aa3a3 100%)}
.hero-title{top:130px;width:1200px;text-align:center;color:var(--white);font-size:57px;font-weight:800;line-height:62px;text-shadow:0 3px 10px rgba(0,0,0,.45)}
.hero-sub{top:276px;width:1200px;text-align:center;color:var(--white);font-size:18px;text-shadow:0 2px 6px rgba(0,0,0,.4)}

/* who */
.who-title{top:726px;left:111px;font-size:33px;font-weight:700;line-height:42px;color:var(--navy)}
.who-copy{top:828px;left:111px;width:470px;font-size:15.5px;line-height:26px}
.who-copy p+p{margin-top:6px}
.check{display:flex;align-items:center;gap:14px;font-size:15.5px}
.check i{width:28px;height:28px;border-radius:50%;border:1px solid var(--line);display:flex;align-items:center;justify-content:center}
.photo{border-radius:12px}
.stat{display:flex;gap:16px;width:300px}
.stat-ic{width:70px;height:70px;border-radius:50%;background:#e4e6e9;flex:none;display:flex;align-items:center;justify-content:center}
.stat h3{font-size:20px;font-weight:600;line-height:25px}
.stat p{font-size:13px;line-height:19px;margin-top:6px;color:var(--muted)}

/* difference */
.diff{top:1390px;left:0;width:1200px;height:749px;background:var(--ice)}
.center{width:1200px;text-align:center;left:0}
.sec-title{font-size:33px;font-weight:700;color:var(--navy)}
.card{background:var(--white);border-radius:14px;border:1px solid #e2ecf1;overflow:hidden;display:flex;width:472px;height:293px}
.card-img{flex:none;width:214px;height:100%;position:relative}
.card-img .go{position:absolute;left:20px;bottom:20px;width:34px;height:34px;background:var(--white);border-radius:6px;display:flex;align-items:center;justify-content:center}
.card-body{flex:1;padding:50px 18px 0 28px}
.card-body h3{font-size:21px;font-weight:600;margin-top:16px}
.card-body p{font-size:13px;line-height:19px;margin-top:10px;color:var(--muted)}
.pill{background:var(--navy);color:var(--white);border-radius:18px;height:33px;padding:0 16px;display:inline-flex;align-items:center;font-size:15px}

/* signature */
.sig{top:2139px;left:0;width:1200px;height:479px;background:linear-gradient(120deg,#2b4d6c 0%,#1d3d5c 45%,#203f5d 100%)}
.sig .eyebrow{color:var(--white);border-color:#8aa0b5}
.tile{width:229px;height:144px;border:1.5px solid #c9d4df;border-radius:10px;display:flex;flex-direction:column;align-items:center;justify-content:flex-start;padding-top:20px;color:var(--white);font-family:'Kumbh Sans',sans-serif;font-weight:600;font-size:19px}
.tile.on{background:var(--white);color:var(--navy)}
.tile .ic{width:70px;height:70px;border-radius:50%;background:var(--white);margin-bottom:14px;display:flex;align-items:center;justify-content:center}
.tile.on .ic{background:var(--navy)}

/* reviews */
.review{width:306px;height:279px;background:var(--ice);border-radius:14px;padding:34px 18px 0 20px}
.review p{font-size:14.5px;line-height:24px;color:var(--muted)}
.reviewer{display:flex;align-items:center;gap:14px;margin-top:22px;position:relative;padding-left:14px}
.avatar{width:64px;height:64px;border-radius:50%;background:linear-gradient(160deg,#b9d6ef,#2c5a88)}
.quote{position:absolute;left:0;top:-12px;width:36px;height:36px;border-radius:50%;background:var(--navy);border:3px solid var(--white);color:var(--white);font-family:'Kumbh Sans',sans-serif;font-weight:800;font-size:22px;display:flex;align-items:center;justify-content:center}
.reviewer b{font-size:14px;color:var(--ink);display:block}
.stars{color:var(--star);font-size:15px;letter-spacing:1px}
.dots{display:flex;gap:10px;align-items:center;justify-content:center}
.dots i{width:9px;height:9px;border-radius:50%;background:#7a8493}
.dots i.on{width:14px;height:14px;background:var(--navy)}

/* footer */
.footer{top:3375px;left:0;width:1200px;height:345px;background:linear-gradient(180deg,#1e3c5a,#1a3653)}
.cta{top:3320px;left:111px;width:978px;height:107px;background:var(--cta-grey);border-radius:12px;display:flex;align-items:center;justify-content:space-between;padding:0 26px 0 29px}
.cta h2{color:var(--white);font-size:31px;font-weight:700}
.foot-nav a{position:absolute;top:3625px;color:var(--white);font-size:18px;text-decoration:none}
</style>
</head>
<body>

<header class="site-header abs">
  <div class="brand abs" style="left:111px;top:22px">
    <span class="brand-dot"></span>
    <div><div class="brand-name">Coral Basins</div><div class="brand-tag">All Your Dreams Come True</div></div>
  </div>
  <nav class="nav">
    <a class="active" style="left:520px">Home</a>
    <a style="left:604px">About</a>
    <a style="left:687px">Services</a>
    <a style="left:785px">Gallery</a>
    <a style="left:877px">Blog</a>
  </nav>
  <span class="btn abs" style="left:950px;top:30px">Contact Us <span class="arrow"><svg width="14" height="14" viewBox="0 0 14 14"><path d="M2 7h9M7 3l4 4-4 4" stroke="#0f2a47" stroke-width="2" fill="none" stroke-linecap="round"/></svg></span></span>
</header>

<section class="hero abs" role="img" aria-label="Photo of a luxury backyard pool with loungers, an umbrella and a stone cabana">
  <h1 class="hero-title abs">The Art of<br>Luxury Pool Design</h1>
  <p class="hero-sub abs">Coral Basins delivers bespoke designs for those who seek the extraordinary.</p>
  <span class="btn abs" style="left:514px;top:316px">Request a Quote <span class="arrow"><svg width="14" height="14" viewBox="0 0 14 14"><path d="M2 7h9M7 3l4 4-4 4" stroke="#0f2a47" stroke-width="2" fill="none" stroke-linecap="round"/></svg></span></span>
</section>

<section class="who">
  <span class="eyebrow abs" style="left:111px;top:670px">WHO WE ARE</span>
  <h2 class="who-title abs">Redefining Luxury, One Pool<br>at a Time.</h2>
  <div class="who-copy abs">
    <p>Lorem ipsum dolor sit amet, consectetur adipiscing elit, sed do eiusmod tempor incididunt ut labore et dolore magna aliqua quis ipsum suspendisse ultrices gravida. Risus commodo viverra maecenas accumsan lacus vel facilisis.</p>
    <p>Sed ut perspiciatis unde omnis iste natus error sit voluptatem accusantium doloremque laudantium,</p>
  </div>
  <div class="check abs" style="left:111px;top:1007px"><i><svg width="12" height="12" viewBox="0 0 12 12"><path d="M2 6l3 3 5-6" stroke="#0f2a47" stroke-width="1.8" fill="none"/></svg></i>Nemo enim ipsam voluptatem quia voluptas</div>
  <div class="check abs" style="left:111px;top:1045px"><i><svg width="12" height="12" viewBox="0 0 12 12"><path d="M2 6l3 3 5-6" stroke="#0f2a47" stroke-width="1.8" fill="none"/></svg></i>Nemo enim ipsam voluptatem quia voluptas</div>
  <span class="btn abs" style="left:111px;top:1097px">Read More <span class="arrow"><svg width="14" height="14" viewBox="0 0 14 14"><path d="M2 7h9M7 3l4 4-4 4" stroke="#0f2a47" stroke-width="2" fill="none" stroke-linecap="round"/></svg></span></span>

  <div class="photo abs" style="left:643px;top:741px;width:186px;height:190px;background:linear-gradient(180deg,#1e8fd6,#4fb7ea)" role="img" aria-label="Lane lines seen under clear pool water"></div>
  <div class="photo abs" style="left:843px;top:680px;width:246px;height:251px;background:linear-gradient(160deg,#5fc0e0,#a9cdd6 60%,#8e9499)" role="img" aria-label="Pool ladder and a red-and-white life ring on the deck"></div>
  <div class="photo abs" style="left:705px;top:937px;width:124px;height:129px;background:linear-gradient(160deg,#2d5a35,#3fbf9f 55%,#7fd8c8)" role="img" aria-label="Green-tinted pool with a ladder among trees"></div>
  <div class="photo abs" style="left:843px;top:937px;width:185px;height:189px;background:linear-gradient(180deg,#8a88a8,#4b4e5c 45%,#2f8fd9 75%,#6fc3f0)" role="img" aria-label="Modern villa with an illuminated infinity pool at dusk"></div>

  <div class="stat abs" style="left:111px;top:1213px"><span class="stat-ic"><svg width="38" height="30" viewBox="0 0 38 30"><ellipse cx="19" cy="9" rx="16" ry="6" fill="none" stroke="#1a1f2b" stroke-width="2"/><path d="M3 9v12c0 3 7 6 16 6s16-3 16-6V9" fill="none" stroke="#1a1f2b" stroke-width="2"/><path d="M10 14v12M19 15v12M28 14v12" stroke="#1a1f2b" stroke-width="2"/></svg></span><div><h3>100+<br>Custom Pools Installed</h3><p>Nemo enim ipsam voluptatem quia voluptas</p></div></div>
  <div class="stat abs" style="left:458px;top:1213px"><span class="stat-ic"><svg width="32" height="32" viewBox="0 0 32 32"><path d="M8 30V16h5l4-10c2 0 3 2 2 5l-1 4h7c2 0 3 2 2 4l-3 9c-1 2-2 2-4 2z" fill="#1a1f2b"/><path d="M5 6l1 2 2 .3-1.5 1.4.4 2.2L5 10.8 3.1 12l.4-2.2L2 8.3 4 8z" fill="#1a1f2b"/><path d="M26 3l1 2 2 .3-1.5 1.4.4 2.2-1.9-1-1.9 1 .4-2.2L23 5.3l2-.3z" fill="#1a1f2b"/></svg></span><div><h3>Over<br>15 Years of Excellence</h3><p>Nemo enim ipsam voluptatem quia voluptas</p></div></div>
  <div class="stat abs" style="left:797px;top:1213px"><span class="stat-ic"><svg width="40" height="28" viewBox="0 0 40 28"><ellipse cx="20" cy="16" rx="17" ry="8" fill="none" stroke="#1a1f2b" stroke-width="2"/><ellipse cx="20" cy="16" rx="10" ry="4" fill="#1a1f2b"/><path d="M24 4v12M30 4v12M24 8h6M24 12h6" stroke="#1a1f2b" stroke-width="2"/></svg></span><div><h3>Serving Elite Homes &amp;<br>Resorts Worldwide</h3><p>Nemo enim ipsam voluptatem quia voluptas</p></div></div>
</section>

<section class="diff abs">
  <div class="abs center" style="top:82px"><span class="eyebrow">ELEGANCE IN WATER</span></div>
  <h2 class="sec-title abs center" style="top:138px">The Coral Difference</h2>
  <p class="abs center" style="top:202px;font-size:15.5px;line-height:26px">Lorem ipsum dolor sit amet, consectetur adipiscing elit, sed do eiusmod tempor incididunt ut labore et dolore<br>magna aliqua quis ipsum suspendisse ultrices gravida.</p>

  <article class="card abs" style="left:111px;top:291px">
    <div class="card-img" style="background:linear-gradient(160deg,#1ea2d8,#55c3e8 60%,#9ad9ec)" role="img" aria-label="Feet splashing in bright turquoise pool water"><span class="go"><svg width="14" height="14" viewBox="0 0 14 14"><path d="M3 11l8-8M5 3h6v6" stroke="#0f2a47" stroke-width="1.8" fill="none"/></svg></span></div>
    <div class="card-body">
      <svg width="100" height="64" viewBox="0 0 100 64"><ellipse cx="50" cy="44" rx="48" ry="18" fill="#0f2a47"/><rect x="54" y="2" width="18" height="34" fill="#fff" stroke="#0f2a47" stroke-width="3"/><path d="M54 12h18M54 22h18" stroke="#0f2a47" stroke-width="3"/></svg>
      <h3>Bespoke Design</h3>
      <p>Sed ut perspiciatis unde omnis iste natus error sit voluptatem accusant doloremque laudantium, totam rem aperiam, eaque ipsa</p>
    </div>
  </article>
  <article class="card abs" style="left:617px;top:291px">
    <div class="card-img" style="background:linear-gradient(180deg,#7a9a58 0%,#c86a8a 22%,#b5b0a5 42%,#3fa9e0 60%,#7cc9f0 100%)" role="img" aria-label="Garden pool with a ladder beside flowering shrubs"><span class="go"><svg width="14" height="14" viewBox="0 0 14 14"><path d="M3 11l8-8M5 3h6v6" stroke="#0f2a47" stroke-width="1.8" fill="none"/></svg></span></div>
    <div class="card-body">
      <svg width="100" height="64" viewBox="0 0 100 64"><path d="M4 62V22h92v40z" fill="none" stroke="#0f2a47" stroke-width="4"/><rect x="4" y="50" width="92" height="12" fill="#0f2a47"/><path d="M30 4v44M48 4v44M30 16h18M30 28h18M30 40h18" stroke="#0f2a47" stroke-width="3"/></svg>
      <h3>Innovation</h3>
      <p>Sed ut perspiciatis unde omnis iste natus error sit voluptatem accusant doloremque laudantium, totam rem aperiam, eaque ipsa</p>
    </div>
  </article>

  <div class="abs" style="left:310px;top:628px;display:flex;align-items:center;gap:16px;font-size:15.5px"><span class="pill">Pure Pool Perfection</span>Trusted By 1000+ Customers For Professional Results.</div>
</section>

<section class="sig abs" role="img" aria-label="Dim underwater pool scene with a ladder rail in the background">
  <span class="eyebrow abs" style="left:111px;top:85px">SIGNATURE COLLECTIONS</span>
  <h2 class="abs" style="left:111px;top:140px;font-size:34px;font-weight:700;line-height:42px;color:#fff">Curated Pools for Discerning<br>Tastes.</h2>
  <p class="abs" style="left:111px;top:246px;width:460px;font-size:15.5px;line-height:26px;color:#fff">Lorem ipsum dolor sit amet, consectetur adipiscing elit, sed do eiusmod tempor incididunt ut labore et dolore magna aliqua qu is ipsum suspendisse ultrices gravida. Risus com modo viv erra maecenas accumsan lacus vel facilisis.</p>
  <span class="btn light abs" style="left:111px;top:359px">View More <span class="arrow"><svg width="14" height="14" viewBox="0 0 14 14"><path d="M2 7h9M7 3l4 4-4 4" stroke="#fff" stroke-width="2" fill="none" stroke-linecap="round"/></svg></span></span>

  <div class="tile abs" style="left:614px;top:88px"><span class="ic"><svg width="36" height="36" viewBox="0 0 36 36"><path d="M4 30h28M6 26h24l-3-12H9z" fill="none" stroke="#0f2a47" stroke-width="2.5"/><path d="M14 4v18M22 4v18M14 10h8M14 16h8" stroke="#0f2a47" stroke-width="2.5"/></svg></span>Infinity Pools</div>
  <div class="tile on abs" style="left:859px;top:88px"><span class="ic"><svg width="40" height="34" viewBox="0 0 40 34"><path d="M6 18c0-8 8-14 16-12s14 8 10 16-14 10-20 8-6-6-6-12z" fill="none" stroke="#fff" stroke-width="2.5"/><path d="M12 20c4-3 8 3 12 0s6-2 8 0" stroke="#fff" stroke-width="2" fill="none"/></svg></span>Indoor Luxury Pools</div>
  <div class="tile abs" style="left:614px;top:250px"><span class="ic"><svg width="34" height="34" viewBox="0 0 34 34"><path d="M4 8h26M4 17h26M4 26h26" stroke="#0f2a47" stroke-width="2.5"/><circle cx="12" cy="8" r="4" fill="#0f2a47"/><circle cx="22" cy="17" r="4" fill="#0f2a47"/><circle cx="14" cy="26" r="4" fill="#0f2a47"/></svg></span>Custom Pools</div>
  <div class="tile abs" style="left:859px;top:250px"><span class="ic"><svg width="36" height="36" viewBox="0 0 36 36"><rect x="6" y="10" width="18" height="22" fill="none" stroke="#0f2a47" stroke-width="2.5"/><path d="M10 15h3M17 15h3M10 21h3M17 21h3M13 32v-5h4v5" stroke="#0f2a47" stroke-width="2.5"/><path d="M28 32V12M28 12c-4 0-6 2-6 4M28 12c4 0 6 2 6 4" stroke="#0f2a47" stroke-width="2" fill="none"/></svg></span>Resort-Style Retreats</div>
</section>

<section class="reviews">
  <div class="abs center" style="top:2698px"><span class="eyebrow">WHY THEY LOVE CORAL BASINS</span></div>
  <h2 class="sec-title abs center" style="top:2758px">Happy Customers</h2>

  <article class="review abs" style="left:111px;top:2840px">
    <p>Sed ut perspiciatis unde omnis iste nat er sit voluptatem accusant doloremque lau dan, totam rem aperiam, eaque ipsa numquam eius modi tempora incidunt ut labore et dolore magnam aliquam</p>
    <div class="reviewer"><span class="quote">“</span><span class="avatar" role="img" aria-label="Customer portrait"></span><div><b>Evan Morris</b><span class="stars">★★★★☆</span></div></div>
  </article>
  <article class="review abs" style="left:448px;top:2840px">
    <p>Sed ut perspiciatis unde omnis iste nat er sit voluptatem accusant doloremque lau dan, totam rem aperiam, eaque ipsa numquam eius modi tempora incidunt ut labore et dolore magnam aliquam</p>
    <div class="reviewer"><span class="quote">“</span><span class="avatar" role="img" aria-label="Customer portrait"></span><div><b>Evan Morris</b><span class="stars">★★★★☆</span></div></div>
  </article>
  <article class="review abs" style="left:784px;top:2840px">
    <p>Sed ut perspiciatis unde omnis iste nat er sit voluptatem accusant doloremque lau dan, totam rem aperiam, eaque ipsa numquam eius modi tempora incidunt ut labore et dolore magnam aliquam</p>
    <div class="reviewer"><span class="quote">“</span><span class="avatar" role="img" aria-label="Customer portrait"></span><div><b>Evan Morris</b><span class="stars">★★★★☆</span></div></div>
  </article>

  <div class="dots abs center" style="top:3157px"><i class="on"></i><i></i><i></i><i></i></div>
  <div class="abs" style="left:310px;top:3202px;display:flex;align-items:center;gap:16px;font-size:15.5px"><span class="pill" style="padding:0 22px">Trust</span><span>1000+ Pool Owners Trust <b style="color:var(--navy);text-decoration:underline">Coral Basins</b> For Crystal-clear Results.</span></div>
</section>

<footer class="footer abs">
  <div class="brand abs" style="left:462px;top:124px">
    <span class="brand-dot" style="background:#fff;width:40px;height:40px"></span>
    <div><div class="brand-name" style="color:#fff;font-size:32px">Coral Basins</div><div class="brand-tag" style="color:#fff;font-size:17px">All Your Dreams Come True</div></div>
  </div>
  <div class="abs" style="left:0;top:293px;width:1200px;height:1px;background:#4d6985"></div>
  <p class="abs center" style="top:308px;font-size:12px;color:#fff">Copyright © 2025 Coral Basins. All rights reserved.</p>
</footer>
<nav class="foot-nav">
  <a style="left:301px">Home</a>
  <a style="left:399px">About</a>
  <a style="left:497px">Services</a>
  <a style="left:613px">Gallery</a>
  <a style="left:721px">Blog</a>
  <a style="left:805px">Contact Us</a>
</nav>

<div class="cta abs">
  <h2>Ready To Design Your Dream Pool?</h2>
  <span class="btn">Book A Consultation <span class="arrow"><svg width="14" height="14" viewBox="0 0 14 14"><path d="M2 7h9M7 3l4 4-4 4" stroke="#0f2a47" stroke-width="2" fill="none" stroke-linecap="round"/></svg></span></span>
</div>

</body>
</html>
```